Stationary Set Rebrand for Brennick

We are a Canadian Distribution and Service Company that was established in 1969. Over the past 5 decades we have expanded our business and have warehouses across Canada. We specialize in adhesive tapes, adhesives, films, safety, warehouse, shipping, janitorial and packaging supplies.

We have updated our logo design and would like a new corporate branding identity that includes a new fresh Stationary Set (Business Cards, Letterhead, Letterhead MS Word, Envelope, Presentation Folders, Email Signatures, Notepad Covers, etc.)

Target Market(s)

Industrial Business Sector

Font styles to use
Sans Serif

Colors
0054AA
0677BA
7BADD7
CADEEF
E8F1F8
0094D4
00A9DD
6FCCEA
C7EBF8
E9F6FB
00AB8E
00BBA5
67D7C9
C6EFE9
E9F9F6
EB3D1F
EC4F4E
F09395
F8D3D4
FCEDEE

Requirements
Should not have
• Colors not too light, darker colours preferred

```html
<!DOCTYPE html>
<html lang="en">
<head>
<meta charset="utf-8">
<title>Brennick Business Card</title>
<link rel="stylesheet" href="https://fonts.googleapis.com/css2?family=Montserrat:wght@400;500;700;800&display=swap">
<style>
  :root {
    --stage: #2b2b2c;
    --card: #161617;
    --card-sheen: #3a3a3c;
    --white: #f4f4f4;
    --soft-white: #d9d9d9;
    --red: #e0202a;
    --silver-light: #e6e6e6;
    --silver-dark: #1c1c1d;
  }
  * { margin: 0; padding: 0; box-sizing: border-box; }
  html, body {
    width: 1200px; height: 689px; overflow: hidden;
    background: var(--stage);
    font-family: "Montserrat", sans-serif;
  }
  .canvas {
    position: relative; width: 1200px; height: 689px;
    display: flex; align-items: center; justify-content: center; gap: 40px;
  }
  .card {
    position: relative; width: 540px; height: 309px;
    border-radius: 20px; overflow: hidden;
    background: var(--card);
    box-shadow: 0 18px 40px rgba(0,0,0,.45);
  }
  /* Front */
  .card--front {
    background: linear-gradient(125deg, var(--card-sheen) 0%, var(--card) 45%, var(--card) 100%);
  }
  .front-name {
    position: absolute; left: 56px; top: 92px;
    font-size: 84px; font-weight: 800; letter-spacing: -2px;
    color: var(--white); line-height: 1;
  }
  .front-services {
    position: absolute; left: 56px; right: 40px; bottom: 46px;
    font-size: 11.5px; font-weight: 400; color: var(--soft-white);
    letter-spacing: .2px;
  }
  /* Back */
  .back-name {
    position: absolute; left: 34px; top: 34px;
    font-size: 44px; font-weight: 800; letter-spacing: -1px;
    color: var(--white); line-height: 1;
  }
  .back-decor {
    position: absolute; right: -40px; top: 30px;
    width: 270px; height: 270px;
  }
  .person {
    position: absolute; left: 34px; top: 118px;
    padding-left: 18px; border-left: 7px solid var(--red);
  }
  .person-name { font-size: 24px; font-weight: 700; color: var(--red); line-height: 1.1; }
  .person-title { font-size: 14px; font-weight: 500; color: var(--white); margin-top: 4px; }
  .address {
    position: absolute; left: 59px; top: 196px;
    font-size: 13px; font-weight: 500; color: var(--white); line-height: 1.45;
  }
  .contacts {
    position: absolute; left: 59px; top: 240px; list-style: none;
    font-size: 13px; font-weight: 500; color: var(--white); line-height: 1.5;
  }
  .contacts li { display: flex; align-items: center; gap: 8px; }
  .contacts svg { width: 12px; height: 12px; fill: var(--red); flex: none; }
</style>
</head>
<body>
<main class="canvas">
  <section class="card card--front" aria-label="Business card front">
    <div class="front-name">Brennick</div>
    <p class="front-services">adhesive tapes, adhesives, films, safety, warehouse, shipping, janitorial and packaging supplies</p>
  </section>

  <section class="card card--back" aria-label="Business card back">
    <svg class="back-decor" viewBox="0 0 270 270" role="img" aria-label="Large glossy brand emblem decoration">
      <defs>
        <linearGradient id="gloss" x1="0" y1="0" x2="1" y2="0">
          <stop offset="0" stop-color="var(--silver-light)"/>
          <stop offset=".45" stop-color="#8a8a8c"/>
          <stop offset="1" stop-color="var(--silver-dark)"/>
        </linearGradient>
      </defs>
      <circle cx="135" cy="135" r="130" fill="url(#gloss)"/>
    </svg>
    <div class="back-name">Brennick</div>
    <div class="person">
      <div class="person-name">Daniel Hartwell</div>
      <div class="person-title">Managing Director</div>
    </div>
    <p class="address">Your address, City<br>State, Zip 1234</p>
    <ul class="contacts">
      <li><svg viewBox="0 0 12 12"><path d="M1 4c0-1.5 2.2-3 5-3s5 1.5 5 3v1H8.5V3.8h-5V5H1zM2 6.2 3.5 5h5L10 6.2V11H2z"/></svg>123 456 789</li>
      <li><svg viewBox="0 0 12 12"><path d="M0 2h12v1L6 7 0 3zM0 4.2 6 8.2l6-4V10H0z"/></svg>info@brennickmail.com</li>
      <li><svg viewBox="0 0 12 12"><circle cx="6" cy="6" r="5.5"/></svg>www.brennickwebsite.com</li>
    </ul>
  </section>
</main>
</body>
</html>
```